HushHarbors.com

Updated Website Structure for HushHarbor.com
1. Home Page

(Add social media links in footer or sidebar)
Suggested addition:

Stay Connected
Follow Hush Harbor for daily encouragement, calming tools, and community stories.

[Facebook Icon] [Instagram Icon] [YouTube Icon]
@HushHarborOfficial

2. How It Works

(No major change — keep focused on process and trust building)

3. Ebook Store

(Add social links at the bottom of the page)

Want more free content?
Follow us on social media for sneak peeks, affirmations, and updates on new releases!

[Facebook] [Instagram] [YouTube]

4. Certification Page

(Optional social proof addition)

Connect with Certified Hush Harbors
Join our online community and see real stories of growth and courage.

Follow us on social media to see how others are supporting each other:

5. Membership Tiers

(Keep page simple, but can include icons in footer)

6. About Me

Suggested addition:

Let’s Stay Connected
I love hearing from others walking this path.

Facebook: @HushHarborOfficial

Instagram: @HushHarborOfficial

YouTube: Hush Harbor Channel

7. Disclosure Page

(Keep links in footer only for professional feel.)

8. Global Footer (Site-wide)

Every page should include a calming footer with:

Navigation links (Home | About Me | How It Works | Ebook Store | Certification | Membership | Disclosure)

Social media icons

Copyright info

Example footer text:

🌿 Walking with fear, choosing courage, calming the nervous system together.

© 2025 HushHarbor.com | All rights reserved

```html
<!DOCTYPE html>
<html lang="en">
<head>
<meta charset="utf-8">
<title>Hush Harbors — Site Pages</title>
<link rel="stylesheet" href="https://fonts.googleapis.com/css2?family=Poppins:wght@400;500;600&family=Lato:wght@400;700&family=Playfair+Display:ital@1&display=swap">
<style>
:root{
  --stage:#ad9fc4;
  --night:#230d26;
  --nav:#1b0a1d;
  --card-dark:#2e1933;
  --mid:#86729a;
  --card-mid:#8d7ca3;
  --btn:#8c77a8;
  --ticker:#d7c3e2;
  --text-light:#f3ecf6;
  --icon-dark:#2a1030;
  --soft:#b9a6cf;
}
*{box-sizing:border-box;margin:0;padding:0}
html,body{width:1200px;height:1200px;overflow:hidden;background:var(--stage)}
body{font-family:'Lato',sans-serif;color:var(--text-light)}
.stage{position:absolute;left:0;top:0;width:1932px;height:1932px;transform:scale(.62112);transform-origin:0 0}
.page{position:absolute;width:446px;overflow:hidden}
.page--left{left:483px;top:8px;height:1909px}
.page--right{left:999px;top:14px;height:1220px}
section{position:relative;width:100%}
h2{font-family:'Poppins',sans-serif;font-weight:500;font-size:13px;text-align:center}
h3{font-family:'Poppins',sans-serif;font-weight:500;font-size:8px}
p{font-size:7px;line-height:1.55}
.btn{display:inline-block;font-family:'Poppins',sans-serif;font-weight:500;font-size:6.5px;color:#fff;background:var(--btn);border-radius:11px;padding:6px 12px}

/* nav */
.nav{height:18px;background:var(--nav);display:flex;align-items:center;gap:9px;padding:0 6px;font-size:4.6px}
.nav span{display:flex;align-items:center;gap:2px}
.nav i{display:inline-block;width:4px;height:4px;background:#ddd;border-radius:1px}
.nav .toggle{margin-left:auto;width:16px;height:7px;border-radius:4px;background:#3c2540;position:relative}
.nav .toggle::after{content:"";position:absolute;right:1px;top:1px;width:5px;height:5px;border-radius:50%;background:#fff}
.ticker{height:14px;margin-top:4px;background:var(--ticker);color:#3a1c40;font-size:4.4px;display:flex;align-items:center;gap:10px;white-space:nowrap;padding-left:0}
.ticker .pill{background:#fff;border-radius:5px;padding:2px 5px;font-weight:700;color:#2a1030}

/* hero */
.hero{height:271px;background:linear-gradient(160deg,#3b1640 0%,#5a3c67 60%,#6a527c 100%)}
.hero__art{position:absolute;left:45px;top:91px;width:148px;height:127px;border-radius:4px;background:radial-gradient(circle at 50% 48%,#e6b7d9 0 32%,#8a789f 33%)}
.hero__copy{position:absolute;left:205px;top:121px;width:200px}
.hero__copy h1{font-family:'Poppins',sans-serif;font-weight:600;font-size:14px;margin-bottom:10px}
.hero__copy p{font-size:5.2px;margin-bottom:8px}
.hero__copy .btn{font-size:4.6px;padding:4px 9px}
.dots{position:absolute;left:215px;top:205px;display:flex;gap:3px}
.dots b{width:3px;height:3px;border-radius:50%;background:#a492b6}
.dots b:last-child{background:#fff}

/* how it works */
.how{height:410px;background:var(--mid)}
.how h2{padding-top:22px}
.lead{text-align:center;font-size:7px;margin-top:9px}
.grid{position:absolute;display:grid;gap:14px}
.how .grid{left:69px;top:88px;grid-template-columns:148px 148px;grid-auto-rows:137px}
.card{border-radius:7px;text-align:center;padding:18px 10px 0}
.card--mid{background:var(--card-mid);box-shadow:0 2px 5px rgba(40,10,45,.35)}
.card svg{width:26px;height:26px;display:block;margin:0 auto 10px}
.card h3{margin-bottom:8px}
.card p{font-size:6.8px;line-height:1.75}

/* ebooks */
.ebooks{height:482px;background:var(--night)}
.ebooks h2{padding-top:38px}
.ebooks .grid{left:87px;top:105px;grid-template-columns:130px 130px;grid-auto-rows:163px;gap:14px}
.card--dark{background:var(--card-dark);border:1px solid #3c2342}
.card--dark svg{fill:var(--btn)}
.card--dark .btn{margin-top:8px}

/* certification */
.cert{height:258px;background:var(--mid)}
.cert h2{position:absolute;left:0;right:0;top:37px}
.cert__badge{position:absolute;left:97px;top:118px;width:34px;height:42px}
.cert__copy{position:absolute;left:231px;top:63px;width:200px}
.cert__copy p{font-size:6.8px;line-height:1.75;margin-bottom:9px}
.btn--night{background:var(--night)}

/* membership */
.tiers{height:452px;background:var(--night)}
.tiers h2{padding-top:36px}
.tiers__grid{position:absolute;left:11px;top:106px;display:grid;grid-template-columns:133px 133px 133px;gap:14px}
.tier{background:var(--card-dark);border:1px solid #3c2342;border-radius:7px;height:303px;text-align:center;padding:20px 12px 0}
.tier svg{width:18px;height:18px;fill:var(--btn);display:block;margin:0 auto 10px}
.tier h3{margin-bottom:8px}
.tier .sub{font-size:6.6px}
.price{font-size:13px;color:var(--soft);margin:20px 0 24px}
.tier ul{list-style:none;text-align:left;font-size:6.2px;line-height:1.6}
.tier li{padding-left:10px;position:relative;margin-bottom:5px}
.tier li::before{content:"✓";position:absolute;left:0;color:var(--soft)}
.tier .btn{margin-top:10px}
.btn--ghost{background:none;border:1px solid var(--soft);color:var(--soft)}

/* about */
.about{height:618px;background:var(--night)}
.about h2{padding-top:37px}
.about__photo{position:absolute;left:39px;top:65px;width:174px;height:174px;border-radius:4px;background:linear-gradient(150deg,#e9d9d7 0%,#d98c84 45%,#b6262a 100%)}
.about__copy{position:absolute;left:225px;top:59px;width:180px}
.about__copy p{font-size:6.1px;line-height:1.7;margin-bottom:8px}
.about__copy .btn{font-size:5.6px;padding:5px 10px}
.disclosure{position:absolute;left:75px;top:304px;width:294px}
.disclosure h2{text-align:left;font-size:11px;line-height:1.4;margin-bottom:6px}
.disclosure h3{font-size:6.6px;line-height:1.2;margin:10px 0 5px}
.disclosure p{font-size:5.8px;line-height:1.7}

/* contact */
.contact{height:378px;background:var(--mid)}
.contact h2{padding-top:27px}
.form{position:absolute;left:89px;top:90px;width:257px}
.form label{display:block;font-size:6.2px;margin-bottom:5px}
.field{height:22px;background:#9484a9;border:1px solid #9d8db1;border-radius:4px;margin-bottom:15px}
.field--area{height:64px}
.form .btn{background:#8876a0;box-shadow:0 1px 3px rgba(40,10,45,.3);margin-top:8px}

/* footer */
.footer{height:224px;background:linear-gradient(180deg,#230d26 0%,#4c3358 50%,#8c7aa1 100%);text-align:center}
.brand{padding-top:28px;display:flex;justify-content:center;align-items:center;gap:6px;font-family:'Poppins',sans-serif;font-weight:600;font-size:12px;color:var(--btn)}
.brand i{width:10px;height:10px;border-radius:50%;background:var(--btn)}
.follow{font-family:'Playfair Display',serif;font-style:italic;font-size:7px;margin-top:12px}
.socials{display:flex;justify-content:center;gap:9px;margin-top:14px}
.socials i{width:16px;height:16px;border-radius:50%;background:#6b5578}
.mission{font-family:'Poppins',sans-serif;font-style:italic;font-weight:500;font-size:8.5px;margin-top:14px}
.quote{font-family:'Playfair Display',serif;font-style:italic;font-size:7px;line-height:1.7;width:230px;margin:9px auto 0}
.footer nav{display:flex;justify-content:center;gap:9px;font-size:6px;margin-top:14px}
.copy{font-size:5.5px;margin-top:17px}
</style>
</head>
<body>
<div class="stage">

  <div class="page page--left">
    <div class="nav">
      <span>✕</span><span><i></i>Home</span><span><i></i>How It Works</span><span><i></i>Ebooks</span><span><i></i>Certification</span><span><i></i>Membership</span><span><i></i>About</span><span><i></i>Disclosure</span><span><i></i>Contact</span>
      <span class="toggle"></span>
    </div>
    <div class="ticker">
      <span>ies here</span><span class="pill">Contact us today</span>
      <span style="margin-left:14px">Mission Statement: Walking with fear. Choosing courage. Calming the nervous system together.</span><span class="pill">Learn more</span>
      <span style="margin-left:14px">Join our supportive community of individu</span>
    </div>

    <section class="hero">
      <div class="hero__art" role="img" aria-label="Illustration of two friends inside a pink heart"></div>
      <div class="hero__copy">
        <h1>Access Helpful Resources</h1>
        <p>Explore our library of ebooks, guides, and tools designed to help you manage anxiety and build resilience.</p>
        <span class="btn">Browse Resources</span>
      </div>
      <div class="dots"><b></b><b></b><b></b></div>
    </section>

    <section class="how">
      <h2>How It Works</h2>
      <p class="lead">Discover the process of building trust and finding calm. Step-by-step guidance to help you on your journey.</p>
      <div class="grid">
        <div class="card card--mid">
          <svg viewBox="0 0 26 26" fill="#2a1030"><circle cx="10" cy="8" r="5"/><path d="M1 23c0-6 4-9 9-9s9 3 9 9z"/><path d="M20 7h2v3h3v2h-3v3h-2v-3h-3v-2h3z"/></svg>
          <h3>Join Our Community</h3>
          <p>Sign up and become part of our supportive network of individuals on similar journeys.</p>
        </div>
        <div class="card card--mid">
          <svg viewBox="0 0 26 26" fill="#2a1030"><path d="M2 5c4-1 8 0 10 2v15c-2-2-6-3-10-2z"/><path d="M24 5c-4-1-8 0-10 2v15c2-2 6-3 10-2z"/></svg>
          <h3>Access Resources</h3>
          <p>Explore our library of ebooks, guides, and tools designed to help you manage anxiety.</p>
        </div>
        <div class="card card--mid">
          <svg viewBox="0 0 26 26" fill="#2a1030"><circle cx="9" cy="13" r="6"/><circle cx="17" cy="13" r="6" fill="#4a2650"/></svg>
          <h3>Connect with Partners</h3>
          <p>Find certified Hush Harbors who can provide guidance, support, and understanding.</p>
        </div>
        <div class="card card--mid">
          <svg viewBox="0 0 26 26" fill="#2a1030"><path d="M13 23 3 13a5.5 5.5 0 0 1 10-7 5.5 5.5 0 0 1 10 7z"/></svg>
          <h3>Grow Together</h3>
          <p>Participate in community events and activities that promote healing and connection.</p>
        </div>
      </div>
    </section>

    <section class="ebooks">
      <h2>Ebook Store</h2>
      <p class="lead">Explore our collection of helpful ebooks to support your journey.</p>
      <div class="grid">
        <div class="card card--dark">
          <svg viewBox="0 0 26 26"><path d="M12 3c-4 0-5 2-5 4-3 1-4 4-3 6-1 2 0 5 3 6 0 3 2 4 5 4z"/><path d="M14 3c4 0 5 2 5 4 3 1 4 4 3 6 1 2 0 5-3 6 0 3-2 4-5 4z"/></svg>
          <h3>Understanding Anxiety</h3>
          <p>A comprehensive guide to recognizing and understanding anxiety patterns.</p>
          <span class="btn">Get This Ebook</span>
        </div>
        <div class="card card--dark">
          <svg viewBox="0 0 26 26"><path d="M4 6l3-3 16 16-3 3z"/><path d="M20 3l3 3-16 16-3-3z"/></svg>
          <h3>Coping Strategies</h3>
          <p>Practical techniques to manage anxiety in daily life.</p>
          <span class="btn">Get This Ebook</span>
        </div>
        <div class="card card--dark">
          <svg viewBox="0 0 26 26"><path d="M13 2 3 6v6c0 6 4 10 10 12 6-2 10-6 10-12V6z"/></svg>
          <h3>Building Resilience</h3>
          <p>Learn how to develop mental and emotional strength to face challenges.</p>
          <span class="btn">Get This Ebook</span>
        </div>
      </div>
    </section>

    <section class="cert">
      <h2>Certification</h2>
      <svg class="cert__badge" viewBox="0 0 34 42" fill="#2a1030"><circle cx="17" cy="15" r="14"/><circle cx="17" cy="15" r="6" fill="#86729a"/><path d="M8 26 4 39l6-3 4 5 3-12zM26 26l4 13-6-3-4 5-3-12z"/></svg>
      <div class="cert__copy">
        <p>Connect with Certified Hush Harbors and join our community of growth and courage.</p>
        <p>Our certification program ensures that all Hush Harbors have completed comprehensive training in anxiety support techniques, active listening, and creating safe spaces for healing conversations.</p>
        <p>Whether you're looking for support or interested in becoming a certified Hush Harbor yourself, we're here to help you on your journey.</p>
        <span class="btn btn--night">Become Certified</span>
      </div>
    </section>

    <section class="tiers">
      <h2>Membership Tiers</h2>
      <p class="lead">Choose the membership level that best supports your needs and enjoy exclusive benefits.</p>
      <div class="tiers__grid">
        <div class="tier">
          <svg viewBox="0 0 18 18"><path d="M8 17V9C4 9 2 6 2 3c4 0 6 2 6 5 0-3 3-6 8-6 0 4-3 7-7 7v8z"/></svg>
          <h3>Basic</h3>
          <p class="sub">For those beginning their journey</p>
          <div class="price">Free</div>
          <ul><li>Access to community forum</li><li>Weekly newsletter</li><li>Basic anxiety management resources</li></ul>
          <span class="btn btn--ghost">Join Now</span>
        </div>
        <div class="tier">
          <svg viewBox="0 0 18 18"><path d="M2 16C3 8 8 3 17 2c0 9-5 14-12 12z"/></svg>
          <h3>Partner</h3>
          <p class="sub">Our most popular option</p>
          <div class="price">$19/month</div>
          <ul><li>All Basic features</li><li>Access to all ebooks</li><li>Monthly group sessions</li><li>Priority forum support</li><li>Discounts on one-on-one sessions</li></ul>
          <span class="btn">Join Now</span>
        </div>
        <div class="tier">
          <svg viewBox="0 0 18 18"><path d="M9 1 4 7h2l-4 5h3l-3 3h6v3h2v-3h6l-3-3h3l-4-5h2z"/></svg>
          <h3>Premium</h3>
          <p class="sub">Complete support package</p>
          <div class="price">$39/month</div>
          <ul><li>All Partner features</li><li>Two one-on-one sessions monthly</li><li>Personalized anxiety management plan</li><li>24/7 crisis chat support</li><li>Early access to new resources</li></ul>
          <span class="btn">Join Now</span>
        </div>
      </div>
    </section>
  </div>

  <div class="page page--right">
    <section class="about">
      <h2>About Me</h2>
      <div class="about__photo" role="img" aria-label="Portrait photo of the founder"></div>
      <div class="about__copy">
        <p>I love hearing from others walking this path. Let's stay connected and support each other.</p>
        <p>My journey with anxiety began over a decade ago, and through my own struggles, I discovered the power of community and shared experiences. What started as personal coping mechanisms evolved into a passion for helping others navigate their anxiety journeys.</p>
        <p>Hush Harbors was born from the belief that no one should face anxiety alone. We're building a community where vulnerability is strength, and support is always available.</p>
        <p>When I'm not working on Hush Harbors, you can find me hiking, practicing mindfulness, or curled up with a good book and my two rescue cats.</p>
        <span class="btn">Get In Touch</span>
      </div>
      <div class="disclosure">
        <h2>Disclosure</h2>
        <p>Read our policies and understand our commitments.</p>
        <h3>Privacy Policy</h3>
        <p>Your privacy is important to us. We are committed to protecting your personal information and being transparent about what data we collect and how we use it.</p>
        <h3>Terms of Service</h3>
        <p>By using our services, you agree to our terms of service. These terms outline the rules and guidelines for using Hush Harbors resources and community.</p>
        <h3>Disclaimer</h3>
        <p>Hush Harbors provides supportive resources and community for anxiety management. We are not a substitute for professional medical advice, diagnosis, or treatment. Always seek the advice of your physician or other qualified health provider with any questions you may have regarding a medical condition.</p>
        <h3>Community Guidelines</h3>
        <p>Our community is built on respect, empathy, and support. We have zero tolerance for harassment, discrimination, or harmful behavior. All members are expected to adhere to our community guidelines.</p>
        <h3>Contact Information</h3>
        <p>If you have any questions about our policies, please contact us at privacy@hushharbors.com.</p>
      </div>
    </section>

    <section class="contact">
      <h2>Contact Us</h2>
      <p class="lead">Have questions or want to get in touch? Send us a message and we'll respond as soon as possible.</p>
      <div class="form">
        <label>Your Name</label><div class="field"></div>
        <label>Email Address</label><div class="field"></div>
        <label>Subject</label><div class="field"></div>
        <label>Your Message</label><div class="field field--area"></div>
        <span class="btn">Send Message</span>
      </div>
    </section>

    <section class="footer">
      <div class="brand"><i></i>Hush Harbors</div>
      <p class="follow">Follow us.</p>
      <div class="socials"><i></i><i></i><i></i></div>
      <p class="mission">Mission Statement</p>
      <p class="quote">"Walking with fear. Choosing courage. Calming the nervous system together."</p>
      <nav><span>Home</span><span>How It Works</span><span>Ebooks</span><span>Certification</span><span>Membership</span><span>About</span><span>Disclosure</span><span>Contact</span></nav>
      <p class="copy">© 2025 HushHarbors.com. All rights reserved.</p>
    </section>
  </div>

</div>
</body>
</html>
```